Business card design for holistic health care clinic

We need a double-sided business card design for our holistic health care clinic that integrates our logo design and also its color scheme. My business is called Valmira. It is an integrative medicine clinic. You have already done the logo for me. Please ensure an elegant and upscale design that is not cluttered, but still has all the necessary information (please see below for details).

Target Market(s)

Wellness, fitness, rehabilitation for educated, well-traveled open-minded clients who are focused on natural, organic, balanced and preventive healthcare and lifestyle.

Industry/Entity Type

Medical

Contact Information for Business Card

Modern, clean.

Number of Pages Required

1 page

Font styles to use
Serif
Sans Serif

Colors

Designer to choose colors to be used in the design.

Requirements
Must have
• Logo on one side, all other information on the other side.
• Other information should include:
• Tobias Wrenfeld - DOE, CPT, LMT
• 4100 East Marrow Drive
• Austin, TX 78119
• 512 555 0148
• 818 555 0192
• info@ValmiraHealth.example
• t.wrenfeld@ValmiraHealth.example
Nice to have
• Darker background on front - but not totally black - shaded/dark gray.

```html
<!DOCTYPE html>
<html lang="en">
<head>
<meta charset="utf-8">
<title>Valmira – Business Card</title>
<link href="https://fonts.googleapis.com/css2?family=Montserrat:ital,wght@0,400;0,700;1,700&family=Open+Sans:wght@400;600&display=swap" rel="stylesheet">
<style>
  :root {
    --brand-blue: #1193cf;
    --paper: #ffffff;
    --ink: #3a3a3a;
    --muted: #6b6b6b;
    --backdrop: #ecedef;
  }
  * { margin: 0; padding: 0; box-sizing: border-box; }
  html, body { width: 1200px; height: 900px; overflow: hidden; }
  body {
    background: var(--backdrop);
    font-family: "Open Sans", Arial, sans-serif;
    position: relative;
  }
  .card {
    position: absolute;
    top: 296px;
    width: 540px;
    height: 309px;
    box-shadow: 0 6px 18px rgba(0,0,0,0.12);
  }
  .card--info { left: 40px; background: var(--paper); }
  .card--brand { left: 620px; background: var(--brand-blue); }

  .person {
    position: absolute;
    left: 150px;
    top: 36px;
    display: flex;
    align-items: baseline;
    gap: 14px;
  }
  .person__name {
    font-family: "Montserrat", Arial, sans-serif;
    font-weight: 700;
    font-style: italic;
    font-size: 15px;
    color: var(--brand-blue);
    text-transform: uppercase;
  }
  .person__creds { font-size: 11px; color: var(--ink); }

  .contact-list {
    position: absolute;
    left: 40px;
    top: 104px;
    list-style: none;
  }
  .contact-list li {
    display: flex;
    align-items: center;
    gap: 9px;
    font-size: 12px;
    line-height: 19px;
    color: var(--ink);
  }
  .contact-list svg { width: 10px; height: 10px; fill: var(--brand-blue); flex: none; }

  .wordmark {
    font-family: "Montserrat", Arial, sans-serif;
    font-weight: 700;
    text-transform: uppercase;
    letter-spacing: 1px;
    line-height: 1;
  }
  .tagline {
    font-family: "Montserrat", Arial, sans-serif;
    font-weight: 700;
    letter-spacing: 0.3px;
  }

  .brand-lockup--info {
    position: absolute;
    left: 300px;
    top: 118px;
    text-align: center;
    color: var(--brand-blue);
  }
  .brand-lockup--info .wordmark { font-size: 40px; }
  .brand-lockup--info .tagline { font-size: 11px; margin-top: 4px; }

  .address {
    position: absolute;
    right: 40px;
    top: 212px;
    text-align: right;
    font-size: 12px;
    line-height: 18px;
    color: var(--ink);
  }

  .brand-lockup--front {
    position: absolute;
    inset: 0;
    display: flex;
    flex-direction: column;
    align-items: center;
    justify-content: center;
    color: var(--paper);
  }
  .brand-lockup--front .wordmark { font-size: 56px; }
  .brand-lockup--front .tagline { font-size: 15px; margin-top: 6px; }
</style>
</head>
<body>
  <section class="card card--info" aria-label="Business card, contact side">
    <div class="person">
      <span class="person__name">Tobias Wrenfeld</span>
      <span class="person__creds">DOE, CPT, LMT</span>
    </div>

    <ul class="contact-list">
      <li><svg viewBox="0 0 10 10"><path d="M2 0.5h2l0.8 2.3-1.2 0.9a5 5 0 0 0 2.7 2.7l0.9-1.2 2.3 0.8v2a1 1 0 0 1-1 1A8.5 8.5 0 0 1 1 1.5a1 1 0 0 1 1-1z"/></svg>512 555 0148</li>
      <li><svg viewBox="0 0 10 10"><path d="M2.5 0h5a0.8 0.8 0 0 1 0.8 0.8v8.4a0.8 0.8 0 0 1-0.8 0.8h-5a0.8 0.8 0 0 1-0.8-0.8V0.8A0.8 0.8 0 0 1 2.5 0zM2.8 1.2v6.6h4.4V1.2z"/></svg>818 555 0192</li>
      <li><svg viewBox="0 0 10 10"><path d="M0 2h10v6H0zM0.8 2.6 5 5.6l4.2-3H0.8z"/></svg>info@ValmiraHealth.example</li>
      <li><svg viewBox="0 0 10 10"><path d="M0 2h10v6H0zM0.8 2.6 5 5.6l4.2-3H0.8z"/></svg>t.wrenfeld@ValmiraHealth.example</li>
      <li><svg viewBox="0 0 10 10"><circle cx="5" cy="5" r="5"/></svg>www.ValmiraHealth.example</li>
    </ul>

    <div class="brand-lockup--info">
      <div class="wordmark">Valmira</div>
      <div class="tagline">Integrative Holistic Medicine</div>
    </div>

    <address class="address" style="font-style:normal">
      4100 East Marrow Drive<br>
      Austin, TX 78119
    </address>
  </section>

  <section class="card card--brand" aria-label="Business card, brand side">
    <div class="brand-lockup--front">
      <div class="wordmark">Valmira</div>
      <div class="tagline">Integrative Holistic Medicine</div>
    </div>
  </section>
</body>
</html>
```